New Business Card Design Project LORVANTI-Italy

we are LORVANTI-Italy
our company in the market for 3 years we are luxury cosmetic company and its about time for a facelift :)
i will like to have elegant luxurious and unique business card
that will give the person that get it a unique, luxurious and elegant impression
I'm VERY OPEN FOR NEW IDEAS , even duo i add a few files of things that i see on line and i like them

i add my logo as well
my website is LORVANTI.COM
(if you would like to see the main style that we have)

Target Market(s)

adult that have money :)

Industry/Entity Type

Business

Contact Information for Business Card

Name - Dario Lorvanti
Position - CEO and CO Founder
address - 4817 E Halvern
telephone - 555-384-1926
email - dario@lorvanti.com
fax - 555-384-1926
website - LORVANTI.COM

Colors
000000
959595
fbee3e
ffffff

Requirements
Must have
• big logo in GOLD color
• elegant look
• impressive
Nice to have
• not must but maybe classy pattern background
• not must but maybe emblem
• maybe clear plastic business card
Should not have
• colors
• images

```html
<!DOCTYPE html>
<html lang="en">
<head>
<meta charset="UTF-8">
<title>LORVANTI Italy – Business Card</title>
<link href="https://fonts.googleapis.com/css2?family=Cormorant+Garamond:wght@500&family=Roboto:wght@400;700&display=swap" rel="stylesheet">
<style>
  :root {
    --backdrop: #2b2b2c;
    --card: #1d1d1e;
    --card-inner: #202021;
    --foil-light: #f2f2f2;
    --foil-mid: #9a9a9a;
    --foil-dark: #3a3a3a;
    --gold: #e8c94a;
    --text-light: #f4f4f4;
    --text-silver: #cfcfcf;
    --text-muted: #959595;
  }
  html, body {
    margin: 0;
    padding: 0;
    width: 1200px;
    height: 900px;
    overflow: hidden;
    background: var(--backdrop);
  }
  .canvas {
    position: relative;
    width: 1200px;
    height: 900px;
    background: var(--backdrop);
  }
  .card {
    position: absolute;
    width: 630px;
    height: 360px;
    background: var(--card);
    box-shadow: 0 14px 30px rgba(0,0,0,0.45);
  }
  .card--front { left: 420px; top: 60px; }
  .card--back  { left: 150px; top: 470px; }

  .foil-frame {
    position: absolute;
    inset: 16px;
    background: linear-gradient(135deg, var(--foil-light) 0%, var(--foil-mid) 35%, var(--foil-dark) 60%, var(--foil-mid) 80%, var(--foil-dark) 100%);
  }
  .card-panel {
    position: absolute;
    inset: 48px;
    background: var(--card-inner);
    outline: 1px solid var(--foil-mid);
  }

  .brand {
    position: absolute;
    left: 0;
    right: 0;
    top: 56px;
    text-align: center;
  }
  .brand-circle {
    display: block;
    width: 64px;
    height: 64px;
    margin: 0 auto 18px;
    border-radius: 50%;
    background: var(--gold);
  }
  .brand-name {
    font-family: "Cormorant Garamond", serif;
    font-weight: 500;
    font-size: 48px;
    letter-spacing: 2px;
    color: var(--gold);
    margin: 0;
    line-height: 1;
  }

  .contact {
    position: absolute;
    left: 0;
    right: 0;
    top: 68px;
    text-align: center;
    font-family: "Roboto", sans-serif;
    color: var(--text-light);
  }
  .contact-name {
    margin: 0;
    font-weight: 700;
    font-size: 21px;
    line-height: 1.2;
    letter-spacing: 0.5px;
    color: var(--text-silver);
  }
  .contact-role {
    margin: 2px 0 20px;
    font-size: 16px;
    line-height: 1.2;
    font-weight: 400;
  }
  .contact-line {
    margin: 0 0 6px;
    font-size: 16px;
    line-height: 1.2;
    font-weight: 400;
  }
</style>
</head>
<body>
<main class="canvas">

  <section class="card card--front" aria-label="Business card front">
    <div class="foil-frame" role="img" aria-label="Silver foil lattice border pattern"></div>
    <div class="card-panel">
      <div class="brand">
        <span class="brand-circle"></span>
        <p class="brand-name">LORVANTI</p>
      </div>
    </div>
  </section>

  <section class="card card--back" aria-label="Business card back">
    <div class="foil-frame" role="img" aria-label="Silver foil lattice border pattern"></div>
    <div class="card-panel">
      <div class="contact">
        <h1 class="contact-name">DARIO LORVANTI</h1>
        <p class="contact-role">CEO &amp; CO Founder</p>
        <p class="contact-line">P.555-384-1926 | F.555-384-1926</p>
        <p class="contact-line">E.dario@lorvanti.com | W.LORVANTI.COM</p>
        <p class="contact-line">4817 E Halvern</p>
      </div>
    </div>
  </section>

</main>
</body>
</html>
```